Simple Commerce Site Design for Clothing & Goodies Brand

NOTE: ONLY COMMUNICATE THROUGH THIS WEBSITE DO NOT CONTACT ME PRIVATELY

I need a website centered around a premium clothing and merchandise brand, specializing in T-shirts and an array of appealing goodies including magnets, tote bags, and kitchen towels. This project aims to design a visually striking, simplistic, and user-friendly layout that captures the essence of our brand, "Les Vignerons de Sainte-Olivette."
Design Requirements
Page Designs
- Home Page: This page should feature a versatile promotional area to highlight special offers or featured products. The design of this zone should be elegant and integrate seamlessly with the rest of the page, drawing inspiration from but refining the approach seen on sites like https://brivo.com

- Product List: Dedicated pages for our primary offerings:

T-shirts in variations for Unisex-Men, Women (with a deep plunge), and Kids
Sweatshirts
Cotton Long Sleeves
Future expansions will include more colors, neck shapes, and items such as hats and polos.

- Goodies Page: Showcasing our range of premium goodies—magnets, tote bags, kitchen towels, and more—with a focus on product visuals and information.

- About/Contact Page: Sharing the story and values behind "Les Vignerons de Sainte-Olivette," along with contact information for customer inquiries.

Design Elements
Color Scheme: The brand's primary color is Panton 2955 (RGB: 33, 59, 99). This should be complemented with colors that enhance the premium feel and readability of the site.

Typography: Select fonts that reflect the brand's premium positioning, ensuring readability and elegance across different devices.

Navigation Bar: The layout must include a simple and straightforward navigation bar at the top of each page, facilitating easy access to all sections of the site without a search feature. This navigation bar should be minimalist and intuitive, allowing for a smooth user journey across the site.

Inspiration and Aesthetics
The site's aesthetic should draw inspiration from the provided examples below, aiming for a clean, modern, and user-centric design. While capturing the essence of those examples, our goal is to exceed them in usability and visual appeal, focusing on a layout that highlights our products and brand story in the most engaging manner.
https://brivo.com/
Similar but more simple design than: https://www.lumeo-mode.com/fr/fr/shop/homme

Industry/Entity Type

Clothing & Goodies Commerce site

Number of Pages Required

4 page

Requirements
Should not have
• Search, complex design

```html
<!DOCTYPE html>
<html lang="fr">
<head>
<meta charset="UTF-8">
<title>Les Vignerons De Sainte-Olivette</title>
<link href="https://fonts.googleapis.com/css2?family=Outfit:wght@400;500;600;700&family=Lato:wght@400;700&display=swap" rel="stylesheet">
<style>
:root{
  --navy:#213b63;
  --navy-deep:#0d2a57;
  --yellow:#fdcb2b;
  --white:#ffffff;
  --ink:#111111;
  --grey-card:#ececec;
  --sky:#a8dcf5;
  --line:#e3e3e3;
}
*{margin:0;padding:0;box-sizing:border-box}
html,body{width:1200px;height:3697px;overflow:hidden}
body{position:relative;background:var(--white);font-family:"Lato",sans-serif;color:var(--ink)}
.abs{position:absolute}
h1,h2,h3,.heading{font-family:"Outfit",sans-serif;font-weight:700}
.btn{position:absolute;display:flex;align-items:center;justify-content:center;border-radius:30px;font-family:"Outfit",sans-serif;font-weight:600;font-size:16px;background:var(--navy-deep);color:var(--white)}
.btn.yellow{background:var(--yellow);color:var(--ink)}

/* top bar */
.topbar{left:0;top:0;width:1200px;height:28px;background:var(--navy-deep);color:var(--white);font-size:15px;display:flex;align-items:center;justify-content:center}
.header{left:0;top:28px;width:1200px;height:84px;background:var(--white);box-shadow:0 1px 3px rgba(0,0,0,.08);z-index:2}
.brand-badge{left:138px;top:7px;width:164px;height:164px;border-radius:50%;background:var(--white);border:6px solid var(--navy);display:flex;align-items:center;justify-content:center;text-align:center;z-index:3;box-shadow:0 3px 10px rgba(0,0,0,.2)}
.brand-badge span{font-family:"Outfit",sans-serif;font-weight:700;color:var(--navy);font-size:17px;line-height:1.2;padding:0 14px}
.nav{left:525px;top:62px;display:flex;gap:40px;font-size:15px;z-index:3}
.nav-icons{left:1028px;top:62px;display:flex;gap:20px;z-index:3}

/* hero */
.hero{left:0;top:112px;width:1200px;height:624px;background:linear-gradient(120deg,#2a211c 0%,#6b3d22 40%,#8a5431 55%,#3a3a36 80%,#2a2d2d 100%)}
.hero-shade{left:0;top:112px;width:1200px;height:624px;background:rgba(0,0,0,.28)}
.hero-eyebrow{left:0;width:1200px;top:278px;text-align:center;color:var(--white);font-family:"Outfit",sans-serif;font-weight:600;font-size:24px}
.hero-title{left:0;width:1200px;top:318px;text-align:center;color:var(--white);font-size:86px;line-height:88px;letter-spacing:-1px}

/* products */
.products-title{left:144px;top:815px;font-size:34px}
.filters{font-family:"Outfit",sans-serif;font-weight:500;font-size:16px}
.filters span{position:absolute;white-space:nowrap}
.card-img{top:917px;width:283px;height:319px;background:var(--grey-card);display:flex;align-items:center;justify-content:center}
.prod{width:190px;height:250px}
.card-name{top:1256px;font-size:26px;font-weight:600}
.card-heart{top:1262px}
.dots{top:1318px;display:flex;gap:6px}
.dots i{display:block;width:12px;height:12px;border-radius:50%}
.price{top:1312px;font-family:"Outfit",sans-serif;font-weight:600;font-size:19px;color:var(--navy);text-align:right;width:100px}
.arrow{width:24px;height:24px;border-radius:50%;display:flex;align-items:center;justify-content:center}

/* about */
.about-band{left:0;top:1434px;width:837px;height:430px;background:var(--yellow)}
.about-title{left:113px;top:1496px;font-size:34px;line-height:46px;color:var(--ink)}
.about-text{left:113px;top:1598px;width:522px;font-size:16.5px;line-height:30px;color:#1a1a1a}
.photo{display:block}

/* offer */
.offer-eyebrow{left:604px;top:2079px;font-family:"Outfit",sans-serif;font-weight:600;font-size:16px;color:var(--navy)}
.offer-title{left:607px;top:2107px;font-size:45px;color:var(--ink)}
.offer-text{left:608px;top:2182px;width:455px;font-size:15px;line-height:33.5px;color:#222}

/* tees band */
.tees-band{left:0;top:2526px;width:1200px;height:548px;background:var(--navy-deep)}
.tees-eyebrow{left:115px;top:2613px;color:var(--white);font-family:"Outfit",sans-serif;font-weight:600;font-size:16px}
.tees-title{left:113px;top:2646px;color:var(--white);font-size:44px;line-height:54px}
.tees-text{left:113px;top:2776px;width:460px;color:var(--white);font-size:15px;line-height:33.5px}

/* footer */
.foot-badge{left:120px;top:3138px;width:210px;height:210px;border-radius:50%;border:6px solid var(--navy);display:flex;align-items:center;justify-content:center;text-align:center}
.foot-badge span{font-family:"Outfit",sans-serif;font-weight:700;color:var(--navy);font-size:22px;line-height:1.25;padding:0 20px}
.news-title{left:452px;top:3157px;font-size:34px}
.news-input{left:453px;top:3232px;width:434px;height:55px;border:1.5px solid #555;display:flex;align-items:center;padding-left:35px;font-size:15px;color:#333}
.news-btn{left:887px;top:3232px;width:182px;height:55px;background:var(--yellow);display:flex;align-items:center;justify-content:center;font-family:"Outfit",sans-serif;font-weight:600;font-size:20px}
.col-title{top:3390px;font-size:20px;font-weight:600}
.col-about{left:128px;top:3430px;width:260px;font-size:13px;line-height:24px}
.links{display:flex;flex-direction:column;gap:11px;font-size:15px}
.links.small{font-size:13px;gap:14px}
.partners{left:127px;top:3518px;display:flex;gap:24px;font-family:"Outfit",sans-serif;font-weight:600;font-size:19px;color:var(--ink);align-items:center}
.social{top:3432px;width:31px;height:31px;border-radius:50%}
.divider{left:110px;top:3605px;width:981px;height:1px;background:var(--line)}
.copyright{left:0;width:1200px;top:3640px;text-align:center;font-size:13px}
</style>
</head>
<body>

<div class="abs topbar">Free Shipping On Orders Over $200</div>
<header class="abs header"></header>
<div class="abs brand-badge"><span>Les Vignerons De Sainte-Olivette</span></div>
<nav class="abs nav"><span>Home</span><span>About Us</span><span>Products</span><span>Contact Us</span></nav>
<div class="abs nav-icons">
  <svg width="16" height="16" viewBox="0 0 16 16"><circle cx="8" cy="4.5" r="3.5" fill="#111"/><path d="M1.5 16c0-4 3-6.5 6.5-6.5s6.5 2.5 6.5 6.5z" fill="#111"/></svg>
  <svg width="18" height="16" viewBox="0 0 18 16"><path d="M1 6h16l-2 9H3z" fill="none" stroke="var(--navy)" stroke-width="1.8" stroke-linejoin="round"/><path d="M5 6l4-5 4 5" fill="none" stroke="var(--navy)" stroke-width="1.8"/><line x1="7" y1="9" x2="7" y2="13" stroke="var(--navy)" stroke-width="1.4"/><line x1="11" y1="9" x2="11" y2="13" stroke="var(--navy)" stroke-width="1.4"/></svg>
</div>

<section>
  <div class="abs hero" role="img" aria-label="Man in a brown wool coat, close-up street portrait"></div>
  <div class="abs hero-shade"></div>
  <p class="abs hero-eyebrow">Welcome To</p>
  <h1 class="abs hero-title">Les Vignerons De<br>Sainte-Olivette</h1>
  <div class="btn" style="left:528px;top:517px;width:145px;height:47px;">Shop Now</div>
</section>

<section>
  <h2 class="abs products-title">Our Products</h2>
  <div class="abs filters" style="left:0;top:832px;">
    <span style="left:755px;color:var(--navy)">ALL</span>
    <span style="left:824px">MEN</span>
    <span style="left:889px">WOMEN</span>
    <span style="left:989px">KIDS</span>
  </div>

  <div class="abs arrow" style="left:45px;top:1057px;background:var(--sky)"><svg width="8" height="10" viewBox="0 0 8 10"><path d="M6 1L2 5l4 4" fill="none" stroke="var(--navy)" stroke-width="1.6"/></svg></div>
  <div class="abs arrow" style="left:1125px;top:1057px;background:var(--navy-deep)"><svg width="8" height="10" viewBox="0 0 8 10"><path d="M2 1l4 4-4 4" fill="none" stroke="#fff" stroke-width="1.6"/></svg></div>

  <div class="abs card-img" style="left:145px"><div class="prod" role="img" aria-label="Navy long sleeve T-shirt" style="background:#1c2540;border-radius:20px 20px 6px 6px;width:190px;height:260px"></div></div>
  <div class="abs card-img" style="left:459px"><div class="prod" role="img" aria-label="Natural cotton tote bag" style="background:#e8e2d4;width:150px;height:170px;margin-top:40px"></div></div>
  <div class="abs card-img" style="left:773px"><div class="prod" role="img" aria-label="Row of colourful kitchen towels" style="background:linear-gradient(90deg,#e6b72a 0 14%,#c9282f 14% 28%,#a82431 28% 42%,#2d3f8f 42% 57%,#c6b896 57% 71%,#6a6e52 71% 85%,#9d8e6b 85%);width:250px;height:120px"></div></div>
  <div class="btn" style="left:530px;top:1053px;width:135px;height:50px;">Shop Now</div>

  <h3 class="abs card-name" style="left:162px">T-shirt</h3>
  <h3 class="abs card-name" style="left:474px">Tote Bags</h3>
  <h3 class="abs card-name" style="left:781px;top:1259px">Kitchen Towels</h3>

  <svg class="abs card-heart" style="left:379px" width="18" height="16" viewBox="0 0 18 16"><path d="M9 14.5S1.5 10 1.5 5.2A3.7 3.7 0 0 1 9 3.8a3.7 3.7 0 0 1 7.5 1.4C16.5 10 9 14.5 9 14.5z" fill="none" stroke="var(--navy)" stroke-width="1.6"/></svg>
  <svg class="abs card-heart" style="left:694px" width="18" height="16" viewBox="0 0 18 16"><path d="M9 14.5S1.5 10 1.5 5.2A3.7 3.7 0 0 1 9 3.8a3.7 3.7 0 0 1 7.5 1.4C16.5 10 9 14.5 9 14.5z" fill="none" stroke="var(--navy)" stroke-width="1.6"/></svg>
  <svg class="abs card-heart" style="left:1005px;top:1265px" width="18" height="16" viewBox="0 0 18 16"><path d="M9 14.5S1.5 10 1.5 5.2A3.7 3.7 0 0 1 9 3.8a3.7 3.7 0 0 1 7.5 1.4C16.5 10 9 14.5 9 14.5z" fill="none" stroke="var(--navy)" stroke-width="1.6"/></svg>

  <div class="abs dots" style="left:163px"><i style="background:var(--yellow)"></i><i style="background:var(--navy-deep)"></i><i style="background:var(--sky)"></i></div>
  <div class="abs dots" style="left:477px"><i style="background:var(--yellow)"></i><i style="background:var(--navy-deep)"></i><i style="background:var(--sky)"></i></div>
  <div class="abs dots" style="left:789px;top:1321px"><i style="background:var(--yellow)"></i><i style="background:var(--navy-deep)"></i><i style="background:var(--sky)"></i></div>
  <p class="abs price" style="left:319px">1800 $</p>
  <p class="abs price" style="left:634px">1800 $</p>
  <p class="abs price" style="left:945px;top:1315px">1800 $</p>
</section>

<section>
  <div class="abs about-band"></div>
  <h2 class="abs about-title">About Les Vignerons De<br>Sainte-Olivette</h2>
  <p class="abs about-text">Lorem ipsum dolor sit amet, consectetur adipiscing elit, sed do eius-mod tempor incididunt ut labore et dolore magna aliqua. Quis ipsum suspendisse ultrices gravida. Risus commodo viverra maecenas ac-cumsan lacus vel facilisis.</p>
  <div class="btn" style="left:110px;top:1744px;width:158px;height:49px;">Learn More</div>
  <div class="abs photo" role="img" aria-label="Man in a white T-shirt on a city street" style="left:673px;top:1471px;width:357px;height:323px;background:linear-gradient(135deg,#4a3e36,#8a7f77 45%,#e9e7e3 60%,#6d5e52)"></div>
  <div class="abs photo" role="img" aria-label="Woman carrying a branded tote bag" style="left:765px;top:1636px;width:326px;height:306px;background:linear-gradient(160deg,#8a5a35,#f0ece4 40%,#d9cdb4 65%,#7e8a9a)"></div>
</section>

<section>
  <div class="abs photo" role="img" aria-label="Three children in pastel coats and knit hats" style="left:0;top:2031px;width:554px;height:410px;background:linear-gradient(90deg,#d8b0a8,#c9a095 35%,#e4c3b5 65%,#d2a99c)"></div>
  <p class="abs offer-eyebrow">We offer</p>
  <h2 class="abs offer-title">15€ Free!</h2>
  <p class="abs offer-text">Lorem ipsum dolor sit amet, consectetur adipiscing elit, sed do eiusmod tempor incididunt ut labore et dolore magna aliqua. Quis ipsum suspendisse ultrices gravida. Risus commodo viverra mae-cenas accumsan lacus vel facilisis.</p>
  <div class="btn" style="left:610px;top:2339px;width:133px;height:49px;">Shop Now</div>
</section>

<section>
  <div class="abs tees-band"></div>
  <p class="abs tees-eyebrow">Shop Now</p>
  <h2 class="abs tees-title">T-Shirts from<br>€ 9.99</h2>
  <p class="abs tees-text">Lorem ipsum dolor sit amet, consectetur adipiscing elit, sed do eiusmod tempor incididunt ut labore et dolore magna aliqua. Quis ipsum suspendisse ultrices gravida. Risus commodo viverra mae-cenas accumsan lacus vel facilisis.</p>
  <div class="btn yellow" style="left:115px;top:2922px;width:133px;height:48px;">Shop Now</div>
  <div class="abs photo" role="img" aria-label="Couple wearing white hoodies on a city street" style="left:644px;top:2592px;width:556px;height:410px;background:linear-gradient(110deg,#9a8a78,#d8d2ca 35%,#efeeec 55%,#6e5440 85%)"></div>
</section>

<footer>
  <div class="abs foot-badge"><span>Les Vignerons De Sainte-Olivette</span></div>
  <h2 class="abs news-title">Sign Up Our Newsletter</h2>
  <div class="abs news-input">Enter Your Email</div>
  <div class="abs news-btn">Subscribe</div>

  <h3 class="abs col-title heading" style="left:129px">About</h3>
  <p class="abs col-about">Lorem ipsum dolor sit amet, consectetur adipiscing elit, sed do eiusmod tempor incididunt ut labore</p>
  <div class="abs partners"><span>Marchéa</span><span>Baylo</span><span style="font-size:14px">Vergerie</span></div>

  <h3 class="abs col-title heading" style="left:460px">Quick Link</h3>
  <div class="abs links" style="left:462px;top:3430px"><span>Home</span><span>About Us</span><span>Products</span><span>Contact Us</span></div>

  <h3 class="abs col-title heading" style="left:659px">Help Link</h3>
  <div class="abs links small" style="left:661px;top:3432px"><span>Support / Contact</span><span>Privacy Policies</span><span>Terms of use</span><span>Return Policy</span></div>

  <h3 class="abs col-title heading" style="left:885px">Follow Us</h3>
  <div class="abs social" style="left:885px;background:var(--navy-deep)"></div>
  <div class="abs social" style="left:924px;background:#dcdcdc"></div>

  <div class="abs divider"></div>
  <p class="abs copyright">© Copyrights 2024 &nbsp;Les Vignerons De Sainte-Olivette &nbsp;| &nbsp;&nbsp; All Rights Reserved</p>
</footer>

</body>
</html>
```